Shopify Web-Page "Tiny-ThreadDays

We are building a new business in Switzerland offering premium sewing holiday camps for kids aged 9–14. In enclosed brief outlines our requirements for a complete Shopify homepage design and a multilingual logo creation.
Domains: tiny-threaddays.ch ; tiny-giornifilo.ch ; tiny-fadentage.ch

Project Overview
We are looking for:
1. A modern, fully designed Shopify homepage in English using standard Shopify content blocks (no custom coding), which we can later update ourselves. Supporting Multilanguage (EN, German, Italian).

2. A logo design that includes the brand identity and communicates our multilingual, creative, and child-focused positioning.

All details in enclosed

```html
<!DOCTYPE html>
<html lang="en">
<head>
<meta charset="utf-8">
<title>Tiny-ThreadDays – Creative Sewing Holidays for Kids</title>
<link href="https://fonts.googleapis.com/css2?family=Roboto:wght@400;500;700;800&family=Inter:wght@400;500;600&display=swap" rel="stylesheet">
<style>
:root{
  --teal:#3aa5aa;
  --teal-dark:#2f8f94;
  --pink:#e06c7a;
  --pink-soft:#f9eded;
  --ink:#1f2328;
  --text:#5b6168;
  --line:#e6e8ea;
  --footer:#2a2b2e;
  --white:#ffffff;
}
*{box-sizing:border-box;margin:0;padding:0}
html,body{width:1200px;height:4656px;overflow:hidden}
body{font-family:"Inter",Arial,sans-serif;color:var(--text);background:var(--white);position:relative;font-size:13px;line-height:1.55}
h1,h2,h3,h4{font-family:"Roboto",Arial,sans-serif;color:var(--ink)}
.accent{color:var(--pink)}
.btn{display:inline-block;background:var(--teal);color:#fff;font-weight:600;font-size:13px;padding:12px 28px;border-radius:24px;text-decoration:none}

/* header */
.site-header{position:absolute;top:0;left:0;width:1200px;height:72px;background:#fff;display:flex;align-items:center;padding:0 140px;justify-content:space-between;box-shadow:0 1px 0 var(--line)}
.brand{display:flex;align-items:center;gap:10px;font-family:"Roboto",sans-serif;font-weight:800;font-size:20px;color:var(--teal)}
.brand-dot{width:14px;height:14px;border-radius:50%;background:var(--pink)}
.main-nav{display:flex;gap:26px;align-items:center;font-size:13px;color:var(--ink)}
.main-nav a{color:var(--ink);text-decoration:none}
.main-nav .active{background:var(--pink-soft);padding:6px 12px;border-radius:4px}
.lang{border:1px solid var(--line);padding:6px 12px;border-radius:4px;font-size:12px}

/* hero */
.hero{position:absolute;top:72px;left:0;width:1200px;height:538px;background:linear-gradient(90deg,#3b2d25 0%,#6a4a36 40%,#b98a62 70%,#d8b48a 100%)}
.hero-photo{position:absolute;inset:0}
.hero-content{position:absolute;left:140px;top:78px;width:460px;color:#fff}
.hero h1{color:#fff;font-size:46px;line-height:1.1;font-weight:800;text-transform:uppercase;margin-bottom:22px}
.hero p{font-size:15px;margin-bottom:20px;color:#f3ece6}
.hero ul{list-style:none;margin-bottom:26px}
.hero li{display:flex;align-items:center;gap:10px;font-size:12px;margin-bottom:10px}
.hero li i{width:14px;height:14px;border-radius:50%;background:var(--teal);display:inline-block}
.scroll-mouse{position:absolute;top:612px;left:585px}

/* about */
.about{position:absolute;top:700px;left:140px;width:920px;height:480px}
.about-img-a{position:absolute;left:0;top:20px;width:230px;height:220px;border-radius:6px;background:linear-gradient(135deg,#e9d8c8,#c9a98a)}
.about-img-b{position:absolute;left:110px;top:150px;width:200px;height:210px;border-radius:6px;border:6px solid #fff;background:linear-gradient(135deg,#d7b79b,#a57a5b)}
.about-text{position:absolute;left:440px;top:20px;width:480px}
.about h2{font-size:30px;text-transform:uppercase;font-weight:800;margin-bottom:16px}
.about p{font-size:12.5px;margin-bottom:12px}

/* how it works */
.how{position:absolute;top:1220px;left:0;width:1200px;height:480px;background:var(--pink-soft);text-align:center}
.section-title{font-size:30px;font-weight:800;text-transform:uppercase;padding-top:60px}
.section-sub{font-size:12.5px;max-width:560px;margin:14px auto 0}
.steps{position:absolute;top:190px;left:130px;width:940px;display:flex;justify-content:space-between}
.step{width:160px;text-align:center}
.step svg{margin-bottom:10px}
.step h4{font-size:13px;margin-bottom:6px}
.step p{font-size:11px}

/* why */
.why{position:absolute;top:1760px;left:0;width:1200px;height:640px;text-align:center}
.why .section-title{padding-top:20px}
.why-grid{position:absolute;top:150px;left:140px;width:920px;display:grid;grid-template-columns:repeat(3,1fr);gap:30px}
.why-card{border:1px solid var(--line);border-radius:8px;height:170px;padding:34px 22px;display:flex;flex-direction:column;align-items:center;gap:18px}
.why-card.featured{border:2px solid var(--pink);box-shadow:0 8px 20px rgba(224,108,122,.15)}
.why-icon{width:48px;height:48px;border-radius:50%;background:#e8f5f5;display:flex;align-items:center;justify-content:center}
.featured .why-icon{background:var(--pink)}
.why-card h4{font-size:13px;font-weight:500;font-family:"Inter",sans-serif}

/* camps */
.camps{position:absolute;top:2420px;left:0;width:1200px;height:500px;text-align:center}
.camps .section-title{padding-top:20px}
.camp-grid{position:absolute;top:140px;left:140px;width:920px;display:grid;grid-template-columns:repeat(3,1fr);gap:26px;text-align:left}
.camp-card{border:1px solid var(--line);border-radius:8px;overflow:hidden;height:330px}
.camp-photo{height:150px}
.camp-body{padding:14px 16px}
.camp-body h3{font-size:14px;margin-bottom:6px}
.camp-body p{font-size:11px;margin-bottom:10px}
.camp-meta{display:grid;grid-template-columns:1fr 1fr;gap:3px 10px;font-size:11px;margin-bottom:12px}
.camp-meta b{color:var(--ink);font-weight:600}
.book-link{color:var(--teal);font-weight:600;font-size:12px;text-decoration:none}

/* faq */
.faq{position:absolute;top:2960px;left:0;width:1200px;height:1080px;text-align:center}
.faq .section-title{padding-top:40px}
.faq-list{position:absolute;top:170px;left:210px;width:780px;text-align:left}
.faq-item{border:1px solid var(--line);border-radius:6px;margin-bottom:14px;padding:18px 22px;display:flex;justify-content:space-between;align-items:flex-start;background:#fff}
.faq-item h4{font-size:14px;font-weight:600}
.faq-item.open{border-left:3px solid var(--pink)}
.faq-item.open p{font-size:12px;margin-top:8px;max-width:640px}

/* cta */
.cta{position:absolute;top:4100px;left:0;width:1200px;height:200px;background:var(--teal);display:flex;align-items:center;justify-content:space-between;padding:0 140px}
.cta h2{color:#fff;font-size:26px;font-weight:800;text-transform:uppercase;margin-bottom:8px}
.cta p{color:#e6f6f6;font-size:13px;max-width:520px}
.btn-light{background:#fff;color:var(--teal)}

/* footer */
.site-footer{position:absolute;top:4300px;left:0;width:1200px;height:356px;background:var(--footer);color:#c9cbce;font-size:12px}
.footer-cols{position:absolute;top:56px;left:140px;width:920px;display:grid;grid-template-columns:220px 150px 230px 1fr;gap:30px}
.footer-brand{font-family:"Roboto",sans-serif;font-weight:800;font-size:24px;color:#fff;margin-bottom:30px;display:flex;align-items:center;gap:10px}
.follow{display:flex;align-items:center;gap:8px}
.social{width:22px;height:22px;border-radius:50%;background:var(--pink)}
.site-footer h4{color:var(--pink);font-size:14px;margin-bottom:16px}
.site-footer ul{list-style:none}
.site-footer li{margin-bottom:10px;display:flex;gap:10px;align-items:flex-start}
.contact-dot{flex:0 0 20px;height:20px;border-radius:50%;background:var(--pink);display:flex;align-items:center;justify-content:center}
.subscribe{display:flex;margin-top:16px;background:#fff;border-radius:20px;padding:4px 4px 4px 14px;align-items:center;justify-content:space-between;color:#999}
.subscribe span.go{width:26px;height:26px;border-radius:50%;background:var(--pink)}
.copyright{position:absolute;bottom:0;left:0;width:1200px;border-top:1px solid #3b3c40;text-align:center;padding:16px 0;font-size:11px}
</style>
</head>
<body>

<header class="site-header">
  <div class="brand"><span class="brand-dot"></span>Tiny-ThreadDays</div>
  <nav class="main-nav">
    <a class="active" href="#">Home</a><a href="#">About Us</a><a href="#">Camps</a><a href="#">How It Works</a><a href="#">FAQs</a><a href="#">Contact</a>
    <span class="lang">English ▾</span>
  </nav>
</header>

<section class="hero">
  <div class="hero-photo" role="img" aria-label="Group of smiling children holding up colourful fabric pieces they sewed"></div>
  <div class="hero-content">
    <h1>Creative Sewing<br>Holidays for Kids</h1>
    <p>Creative fun in Zurich – Multilingual and inspiring. Learn sewing, build confidence, and create unique fashion pieces in small group camps!</p>
    <ul>
      <li><i></i>Crafting Fun, One Stitch at a Time</li>
      <li><i></i>Multilingual Creativity Made Just for Kids</li>
    </ul>
    <a class="btn" href="#">View Upcoming Camps</a>
  </div>
</section>

<svg class="scroll-mouse" width="30" height="44" viewBox="0 0 30 44" aria-hidden="true"><rect x="2" y="2" width="26" height="40" rx="13" fill="none" stroke="#1f2328" stroke-width="2"/><rect x="13" y="10" width="4" height="9" rx="2" fill="#1f2328"/></svg>

<section class="about">
  <div class="about-img-a" role="img" aria-label="Girl sewing at a machine with fabric"></div>
  <div class="about-img-b" role="img" aria-label="Two children working on a sewing project together"></div>
  <div class="about-text">
    <h2>About Our <span class="accent">Camps</span></h2>
    <p>At Tiny-ThreadDays, we believe in nurturing creativity while having fun. Our experienced instructors create a safe, inspiring environment where children can explore their creative potential.</p>
    <p>With over 10 years of experience in teaching children sewing, tailoring, and design, Carla and her team bring joy through a creative week of vacation – with real results: self-sewn pieces, new friends, and lots of pride.</p>
    <p>At the last day, the children show off their success, their own sewn unique pieces, in a sympathetic fashion show. Join our premium sewing camps in Zurich where children ages 9–14 discover creativity, build confidence, and make new friends while learning to sew in a fun, supportive environment.</p>
    <a class="btn" href="#" style="margin-top:10px">Book camp Now</a>
  </div>
</section>

<section class="how">
  <h2 class="section-title">How Our Camps <span class="accent">Work</span></h2>
  <p class="section-sub">Carla and her team bring over 10 years of experience teaching children sewing, tailoring, and design with fun, style, and structure.</p>
  <div class="steps">
    <div class="step">
      <svg width="40" height="40" viewBox="0 0 40 40" fill="none" stroke="#e06c7a" stroke-width="2"><rect x="8" y="6" width="24" height="28" rx="2"/><path d="M13 14h14M13 20h14M13 26h9"/></svg>
      <h4>Project Selection</h4><p>Your child chooses their own model based on previously produced clothing items and sewing patterns.</p>
    </div>
    <div class="step">
      <svg width="40" height="40" viewBox="0 0 40 40" fill="none" stroke="#e06c7a" stroke-width="2"><path d="M6 30l10-20 8 12 4-6 6 14z"/></svg>
      <h4>Fabric selection</h4><p>High-quality fabrics are available.</p>
    </div>
    <div class="step">
      <svg width="40" height="40" viewBox="0 0 40 40" fill="none" stroke="#e06c7a" stroke-width="2"><path d="M6 32h28M10 32V12h22v8H18v12"/><path d="M26 20v6"/></svg>
      <h4>Sewing machine</h4><p>Learn how to use a sewing machine.</p>
    </div>
    <div class="step">
      <svg width="40" height="40" viewBox="0 0 40 40" fill="none" stroke="#e06c7a" stroke-width="2"><circle cx="12" cy="28" r="5"/><circle cx="28" cy="28" r="5"/><path d="M15 24L30 6M25 24L10 6"/></svg>
      <h4>Sewing &amp; refining</h4><p>Step by step to the goal with professional guidance.</p>
    </div>
    <div class="step">
      <svg width="40" height="40" viewBox="0 0 40 40" fill="none" stroke="#e06c7a" stroke-width="2"><path d="M14 6l-8 6 4 6 3-2v18h14V16l3 2 4-6-8-6c-1 3-3 4-6 4s-5-1-6-4z"/></svg>
      <h4>Showtime!</h4><p>Fashion show or photo shoot at the end of the week.</p>
    </div>
  </div>
</section>

<section class="why">
  <h2 class="section-title">Why Parents <span class="accent">Choose Us</span></h2>
  <p class="section-sub">Why families love Tiny-ThreadDays Sewing Camps: small groups of maximum 8 children for personalized attention</p>
  <div class="why-grid">
    <div class="why-card"><div class="why-icon"><svg width="24" height="24" viewBox="0 0 24 24" fill="none" stroke="#3aa5aa" stroke-width="2"><circle cx="8" cy="8" r="3"/><circle cx="16" cy="8" r="3"/><path d="M2 20c0-4 3-6 6-6s6 2 6 6M12 16c1-1 2-2 4-2 3 0 6 2 6 6"/></svg></div><h4>Small groups &amp; personalized attention</h4></div>
    <div class="why-card featured"><div class="why-icon"><svg width="24" height="24" viewBox="0 0 24 24" fill="none" stroke="#fff" stroke-width="2"><path d="M3 5h10M8 3v2M5 5c1 4 4 7 7 8M11 5c-1 4-4 7-7 8M13 21l4-10 4 10M14.5 17h5"/></svg></div><h4>Multilingual supervision<br>(DE / EN / IT)</h4></div>
    <div class="why-card"><div class="why-icon"><svg width="24" height="24" viewBox="0 0 24 24" fill="none" stroke="#3aa5aa" stroke-width="2"><path d="M12 22s7-7 7-12a7 7 0 0 0-14 0c0 5 7 12 7 12z"/><circle cx="12" cy="10" r="2.5"/></svg></div><h4>Pick-up Service from the Main-Station</h4></div>
    <div class="why-card"><div class="why-icon"><svg width="24" height="24" viewBox="0 0 24 24" fill="none" stroke="#3aa5aa" stroke-width="2"><path d="M12 3l2.8 5.8 6.2.9-4.5 4.4 1 6.2L12 17.4 6.5 20.3l1-6.2L3 9.7l6.2-.9z"/></svg></div><h4>Encouragement of creativity, self-confidence, and fine motor skills</h4></div>
    <div class="why-card"><div class="why-icon"><svg width="24" height="24" viewBox="0 0 24 24" fill="none" stroke="#3aa5aa" stroke-width="2"><path d="M12 3l8 3v6c0 5-3.5 8-8 9-4.5-1-8-4-8-9V6z"/><path d="M8.5 12l2.5 2.5 4.5-5"/></svg></div><h4>Safe, loving environment in Zurich, various places easy to reach</h4></div>
    <div class="why-card"><div class="why-icon"><svg width="24" height="24" viewBox="0 0 24 24" fill="none" stroke="#3aa5aa" stroke-width="2"><path d="M4 20h16M6 20V8h13v5H10v7"/><path d="M16 13v4"/></svg></div><h4>High-quality fabrics &amp; top-quality sewing machines (Stitchwell)</h4></div>
  </div>
</section>

<section class="camps">
  <h2 class="section-title">Our Upcoming <span class="accent">Camps</span></h2>
  <p class="section-sub">Real results: self-sewn pieces, new friends, and lots of pride. Culminating fashion show to celebrate achievements</p>
  <div class="camp-grid">
    <article class="camp-card">
      <div class="camp-photo" role="img" aria-label="Children sewing at a table in a bright classroom" style="background:linear-gradient(135deg,#c8d8cf,#8aa89a)"></div>
      <div class="camp-body">
        <h3>Spring Sewing Camp</h3>
        <p>Join us for a creative week during spring break! Children will learn sewing basics and create their own spring-themed projects.</p>
        <div class="camp-meta"><span><b>Age:</b> 9D to 14</span><span><b>Total:</b> 200 Kids</span><span><b>Date:</b> 01 Oct,2025</span><span><b>Duration:</b> 08 Days</span></div>
        <a class="book-link" href="#">Book Now →</a>
      </div>
    </article>
    <article class="camp-card">
      <div class="camp-photo" role="img" aria-label="Group of kids showing their finished summer garments" style="background:linear-gradient(135deg,#e8d3a6,#b99a63)"></div>
      <div class="camp-body">
        <h3>Summer Fashion Camp</h3>
        <p>Our popular summer program where kids design and create their own summer wardrobe items in a fun, supportive environment.</p>
        <div class="camp-meta"><span><b>Age:</b> 9D to 14</span><span><b>Total:</b> 200 Kids</span><span><b>Date:</b> 01 Jul,2025</span><span><b>Duration:</b> 08 Days</span></div>
        <a class="book-link" href="#">Book Now →</a>
      </div>
    </article>
    <article class="camp-card">
      <div class="camp-photo" role="img" aria-label="Children working on autumn-coloured fabric projects" style="background:linear-gradient(135deg,#e3c0a4,#a8755a)"></div>
      <div class="camp-body">
        <h3>Autumn Creative Camp</h3>
        <p>Get ready for cooler weather by creating cozy autumn accessories and clothing items in this creative camp Autumn Creative Camp.</p>
        <div class="camp-meta"><span><b>Age:</b> 9D to 14</span><span><b>Total:</b> 200 Kids</span><span><b>Date:</b> 01 Oct,2025</span><span><b>Duration:</b> 08 Days</span></div>
        <a class="book-link" href="#">Book Now →</a>
      </div>
    </article>
  </div>
</section>

<section class="faq">
  <h2 class="section-title">Frequently Asked Questions</h2>
  <p class="section-sub">Real results: self-sewn pieces, new friends, and lots of pride. Culminating fashion show to celebrate achievements</p>
  <div class="faq-list">
    <div class="faq-item open"><div><h4>Does my child need any prior knowledge?</h4><p>No. We welcome children aged 9–14 years. This age range ensures that participants have the fine motor skills needed for sewing while still being excited about creative projects.</p></div><span>⌃</span></div>
    <div class="faq-item"><h4>How does the pick-up service work?</h4><span>⌄</span></div>
    <div class="faq-item"><h4>How many items of clothing are produced?</h4><span>⌄</span></div>
    <div class="faq-item"><h4>What should my child bring to camp?</h4><span>⌄</span></div>
    <div class="faq-item"><h4>What are the camp hours?</h4><span>⌄</span></div>
    <div class="faq-item"><h4>We offer pick-up from Zurich Main Station at times. Parents can arrange this during booking</h4><span>⌄</span></div>
    <div class="faq-item"><h4>What is your cancellation policy?</h4><span>⌄</span></div>
    <div class="faq-item"><h4>How many items of clothing are produced?</h4><span>⌄</span></div>
    <div class="faq-item"><h4>Each child completes their own unique clothing item during the week</h4><span>⌄</span></div>
    <div class="faq-item"><h4>What safety measures are in place?</h4><span>⌄</span></div>
  </div>
</section>

<section class="cta">
  <div>
    <h2>Ready for a Creative Adventure?</h2>
    <p>Spaces are limited to 8 children per camp to ensure personalized attention. Book now to secure your child's spot!</p>
  </div>
  <a class="btn btn-light" href="#">View All Camps</a>
</section>

<footer class="site-footer">
  <div class="footer-cols">
    <div>
      <div class="footer-brand"><span class="brand-dot"></span>Tiny-ThreadDays</div>
      <div class="follow">Follow Us <span class="social"></span><span class="social"></span><span class="social"></span></div>
    </div>
    <div>
      <h4>Quick Links</h4>
      <ul><li>Home</li><li>About Us</li><li>Camps</li><li>How It Works</li><li>Contact</li></ul>
    </div>
    <div>
      <h4>Contact Us</h4>
      <ul>
        <li><span class="contact-dot"></span>Fadenweg 7, 8001 Zurich, Switzerland</li>
        <li><span class="contact-dot"></span>Phone: +41 44 555 01 20</li>
        <li><span class="contact-dot"></span>info@tiny-threaddays.ch</li>
      </ul>
    </div>
    <div>
      <h4>Subscribe to newsletter</h4>
      <p>Latest updates, exclusive content, and special offers! Subscribe to our newsletter!</p>
      <div class="subscribe">Your email <span class="go"></span></div>
    </div>
  </div>
  <div class="copyright">© 2025 Tiny-ThreadDays. All Rights Reserved.</div>
</footer>

</body>
</html>
```